Business Card for Industrial Distributor

We need a business card design for an industrial distributor. We sell machine parts for the manufacturing and oil industry. We would like the cards to look clean and modern but with a touch of industry.

Our colors are blue/white.

Please feel free to visit our website www.korvelpartsco.com

Target Market(s)

mexican manufacturers in the automobile/aerospace industry

Industry/Entity Type

Industrial

Colors
ffffff
0555a3

```html
<!DOCTYPE html>
<html lang="en">
<head>
<meta charset="utf-8">
<title>Korvel Business Card</title>
<link rel="stylesheet" href="https://fonts.googleapis.com/css2?family=Open+Sans:wght@400;600;700;800&display=swap">
<style>
  :root {
    --stage: #e4e7ec;
    --brand-blue: #0555a3;
    --brand-blue-deep: #044a8f;
    --ink: #ffffff;
    --ink-soft: #dbe6f3;
    --emboss: #0a63b8;
    --emboss-text: #1a6fc0;
  }
  * { box-sizing: border-box; margin: 0; padding: 0; }
  html, body { width: 1200px; height: 844px; overflow: hidden; }
  body {
    background: var(--stage);
    font-family: "Open Sans", sans-serif;
    position: relative;
  }
  .card {
    position: absolute;
    top: 273px;
    width: 520px;
    height: 297px;
    border-radius: 3px;
    box-shadow: 0 6px 18px rgba(0,0,0,0.22);
  }
  .card-front { left: 60px; background: var(--brand-blue); color: var(--ink); }
  .card-back { left: 620px; background: var(--brand-blue-deep); }

  .phones {
    position: absolute; top: 22px; right: 24px;
    font-size: 13px; line-height: 18px; text-align: right; color: var(--ink-soft);
  }
  .phones li { list-style: none; display: flex; align-items: center; justify-content: flex-end; gap: 6px; }
  .phones svg { width: 10px; height: 10px; fill: var(--ink-soft); }

  .person { position: absolute; left: 30px; top: 80px; }
  .person-name { font-size: 15px; font-weight: 700; line-height: 20px; }
  .person-title { font-size: 13px; line-height: 18px; color: var(--ink-soft); }

  .brand {
    position: absolute; left: 100px; top: 124px;
    display: flex; align-items: center; gap: 10px;
  }
  .brand-dot { width: 58px; height: 58px; border-radius: 50%; background: var(--ink); }
  .brand-name { font-size: 46px; line-height: 60px; font-weight: 800; letter-spacing: -1px; color: var(--ink); }

  .address {
    position: absolute; right: 26px; top: 196px;
    font-size: 12px; line-height: 16px; text-align: right; color: var(--ink-soft);
  }

  .links { position: absolute; left: 30px; bottom: 20px; font-size: 15px; line-height: 20px; }
  .links li { list-style: none; display: flex; align-items: center; gap: 8px; }
  .links svg { width: 10px; height: 10px; fill: var(--ink); flex: none; }

  .back-brand {
    position: absolute; inset: 0;
    display: flex; flex-direction: column; align-items: center; justify-content: center; gap: 10px;
  }
  .back-dot { width: 96px; height: 96px; border-radius: 50%; background: var(--emboss); }
  .back-name { font-size: 22px; font-weight: 800; color: var(--emboss-text); }
</style>
</head>
<body>
  <section class="card card-front">
    <ul class="phones">
      <li>312-555-0142
        <svg viewBox="0 0 10 10"><path d="M2 1h2l1 2-1 1a5 5 0 0 0 2 2l1-1 2 1v2c0 .6-.4 1-1 1A8 8 0 0 1 1 2c0-.6.4-1 1-1z"/></svg>
      </li>
      <li>312-555-01873
        <svg viewBox="0 0 10 10"><path d="M3 0h4a1 1 0 0 1 1 1v8a1 1 0 0 1-1 1H3a1 1 0 0 1-1-1V1a1 1 0 0 1 1-1zm0 1.5v6h4v-6z"/></svg>
      </li>
    </ul>

    <div class="person">
      <p class="person-name">Dana Ortiz, Ph.D.</p>
      <p class="person-title">Administrator</p>
    </div>

    <div class="brand">
      <span class="brand-dot"></span>
      <span class="brand-name">Korvel</span>
    </div>

    <p class="address">240 W.Harmon Suite 318.<br>Dayton, Ohio 45402</p>

    <ul class="links">
      <li>
        <svg viewBox="0 0 10 10"><path d="M0 1h10v8H0zm1 1v.4l4 2.6 4-2.6V2z"/></svg>
        info@yourname.com
      </li>
      <li>
        <svg viewBox="0 0 10 10"><path d="M5 0a5 5 0 1 0 0 10A5 5 0 0 0 5 0zm0 1c.6.8 1 2 1.1 3.5H3.9C4 3 4.4 1.8 5 1zM1 5.5h2c0 1.3.4 2.5.9 3.3A4 4 0 0 1 1 5.5zm0-1a4 4 0 0 1 2.9-3.3c-.5.8-.9 2-.9 3.3zm4 4.5c-.6-.8-1-2-1.1-3.5h2.2C6 7 5.6 8.2 5 9zm1.1-.2c.5-.8.9-2 .9-3.3h2a4 4 0 0 1-2.9 3.3zM7 4.5c0-1.3-.4-2.5-.9-3.3A4 4 0 0 1 9 4.5z"/></svg>
        www.korvelpartsco.com
      </li>
    </ul>
  </section>

  <section class="card card-back">
    <div class="back-brand">
      <span class="back-dot"></span>
      <span class="back-name">Korvel</span>
    </div>
  </section>
</body>
</html>
```